Business Card Design

The Kestrel Lodge Inn is the most centrally located motel in Grafton.
We are the only family owned motel in Grafton.
Our colour scheme is blue, whiteand black.

I have uploaded a photo of our new rooms and the logo for you to use Thanks. Looking good

Industry/Entity Type

Motel

Contact Information for Business Card

The Kestrel Lodge Inn
Gareth & Lorna Pelling
Owner/Operators
14-16 Wexbury Lane, Grafton NSW 2460
Ph: 02 6617 3904
Email: thekestrellodgeinn@mailvista.example
reception@kestrellodgeinn.example.au
www.kestrellodgeinn.example.au

Colors
0392cd
0455a3

```html
<!DOCTYPE html>
<html lang="en">
<head>
<meta charset="utf-8">
<title>The Kestrel Lodge Inn – Business Card</title>
<link href="https://fonts.googleapis.com/css2?family=Montserrat:wght@500;700&display=swap" rel="stylesheet">
<style>
  :root {
    --page-bg: #e9e7e4;
    --card-bg: #ffffff;
    --brand-dark: #0455a3;
    --brand-light: #0392cd;
    --ink: #2a2a2a;
    --ink-soft: #555555;
    --on-band: #ffffff;
  }
  html, body {
    margin: 0;
    width: 1200px;
    height: 900px;
    overflow: hidden;
    background: var(--page-bg);
    font-family: "Montserrat", Arial, sans-serif;
  }
  .stage {
    width: 1200px;
    height: 900px;
    display: flex;
    align-items: center;
    justify-content: center;
  }
  .business-card {
    position: relative;
    width: 840px;
    height: 480px;
    background: var(--card-bg);
    box-shadow: 0 10px 30px rgba(0,0,0,0.15);
    overflow: hidden;
  }
  .brand-mark {
    position: absolute;
    top: 120px;
    left: 0;
    right: 0;
    display: flex;
    align-items: center;
    justify-content: center;
    gap: 14px;
  }
  .brand-dot {
    width: 34px;
    height: 34px;
    border-radius: 50%;
    background: var(--brand-dark);
  }
  .brand-name {
    font-weight: 700;
    font-size: 34px;
    color: var(--brand-dark);
    letter-spacing: 0.5px;
  }
  .person-line {
    position: absolute;
    top: 218px;
    left: 0;
    right: 0;
    text-align: center;
    font-weight: 500;
    font-size: 15px;
    font-variant: small-caps;
    letter-spacing: 2.5px;
    color: var(--ink);
  }
  .person-line .divider {
    display: inline-block;
    width: 1px;
    height: 16px;
    background: var(--ink);
    margin: 0 12px;
    vertical-align: -3px;
  }
  .contact-block {
    position: absolute;
    top: 318px;
    left: 60px;
    font-size: 11px;
    font-weight: 500;
    font-variant: small-caps;
    letter-spacing: 1.2px;
    color: var(--ink-soft);
    line-height: 24px;
  }
  .contact-row { display: flex; align-items: center; gap: 14px; }
  .contact-item { display: inline-flex; align-items: center; gap: 5px; }
  .contact-icon { width: 12px; height: 12px; flex: none; }
  .accent-band {
    position: absolute;
    left: 0;
    bottom: 0;
    width: 840px;
    height: 200px;
  }
  .band-url {
    position: absolute;
    right: 70px;
    bottom: 72px;
    font-size: 15px;
    font-weight: 500;
    font-variant: small-caps;
    letter-spacing: 3px;
    color: var(--on-band);
    transform: rotate(-13deg);
    transform-origin: right bottom;
  }
</style>
</head>
<body>
<main class="stage">
  <section class="business-card" aria-label="Business card for The Kestrel Lodge Inn">

    <div class="brand-mark">
      <span class="brand-dot" aria-hidden="true"></span>
      <span class="brand-name">The Kestrel Lodge Inn</span>
    </div>

    <p class="person-line">Tom Avery<span class="divider"></span>Owner / C.E.O</p>

    <div class="contact-block">
      <div class="contact-row">
        <span class="contact-item">
          <svg class="contact-icon" viewBox="0 0 12 12" aria-hidden="true"><circle cx="6" cy="6" r="6" fill="#444"/><path d="M6 2.5a2 2 0 0 0-2 2c0 1.6 2 4.5 2 4.5s2-2.9 2-4.5a2 2 0 0 0-2-2z" fill="#fff"/></svg>
          Suite # 118, Elm Court, NY 40217
        </span>
        <span class="contact-item">
          <svg class="contact-icon" viewBox="0 0 12 12" aria-hidden="true"><circle cx="6" cy="6" r="6" fill="#444"/><circle cx="6" cy="6" r="3.2" fill="none" stroke="#fff" stroke-width="0.9"/><line x1="2.8" y1="6" x2="9.2" y2="6" stroke="#fff" stroke-width="0.9"/></svg>
          www.Samplesite.example
        </span>
      </div>
      <div class="contact-row">
        <span class="contact-item">
          <svg class="contact-icon" viewBox="0 0 12 12" aria-hidden="true"><circle cx="6" cy="6" r="6" fill="#444"/><path d="M4 3l1.2 1.4-.6.9c.5 1 1.1 1.6 2.1 2.1l.9-.6L9 8l-.8 1C5.6 8.6 3.4 6.4 3 3.8z" fill="#fff"/></svg>
          555-201-4410
        </span>
        <span class="contact-item">
          <svg class="contact-icon" viewBox="0 0 12 12" aria-hidden="true"><circle cx="6" cy="6" r="6" fill="#444"/><rect x="4" y="2.5" width="4" height="7" rx="0.8" fill="#fff"/></svg>
          555-382-6127
        </span>
        <span class="contact-item">
          <svg class="contact-icon" viewBox="0 0 12 12" aria-hidden="true"><circle cx="6" cy="6" r="6" fill="#444"/><rect x="3" y="4" width="6" height="4.5" fill="#fff"/></svg>
          555-947-0356
        </span>
        <span class="contact-item">
          <svg class="contact-icon" viewBox="0 0 12 12" aria-hidden="true"><circle cx="6" cy="6" r="6" fill="#444"/><rect x="2.8" y="3.8" width="6.4" height="4.4" fill="#fff"/><path d="M2.8 3.8L6 6.4l3.2-2.6" fill="none" stroke="#444" stroke-width="0.7"/></svg>
          name@samplesite.example
        </span>
      </div>
    </div>

    <svg class="accent-band" viewBox="0 0 840 200" preserveAspectRatio="none" aria-hidden="true">
      <defs>
        <linearGradient id="bandFill" x1="0" y1="1" x2="1" y2="0">
          <stop offset="0" stop-color="var(--brand-dark)"/>
          <stop offset="0.55" stop-color="var(--brand-light)"/>
          <stop offset="1" stop-color="var(--brand-dark)"/>
        </linearGradient>
      </defs>
      <path d="M0 200 L0 188 Q 460 180 840 10 L840 200 Z" fill="url(#bandFill)"/>
    </svg>
    <p class="band-url">www.Samplesite.example</p>

  </section>
</main>
</body>
</html>
```